Business cards and stationary design

We just completed the design of our new logo and we need to print new business cards and letterhead for our nonprofit. We are looking for a fresh new design that shows off our new logo. On letterhead, we must have a column on the right or left to include our Board of Directors (up to 45 names) (see attachment)

Industry/Entity Type

Non-Profit

Contact Information for Business Card

Standard business card with name, title, Company name, mailing address phone numbers, email address and website. Tagline on back "Bringing the homeless home"

Font styles to use
Sans Serif

Requirements
Must have
• include pertinent information above
• new logo
• fonts compatible with logo
• should use logo colors only
Nice to have
• tag lines

```html
<!DOCTYPE html>
<html lang="en">
<head>
<meta charset="utf-8">
<title>Harbor Home Alliance — Business Card</title>
<link rel="stylesheet" href="https://fonts.googleapis.com/css2?family=Roboto:wght@400;500;700&family=Roboto+Condensed:wght@500;700&display=swap">
<style>
  :root {
    --teal: #0a7fa0;
    --red: #d81e2a;
    --paper: #f2f2f2;
    --ink: #4a4a4a;
    --ink-strong: #3c3c3c;
    --backdrop: #2e2e2e;
    --white: #ffffff;
  }
  * { margin: 0; padding: 0; box-sizing: border-box; }
  html, body {
    width: 1200px; height: 960px; overflow: hidden;
    background: var(--backdrop);
    font-family: "Roboto", Arial, sans-serif;
  }
  .canvas { position: relative; width: 1200px; height: 960px; }

  .card {
    position: absolute; left: 320px; width: 600px; height: 342px;
    border-radius: 16px; overflow: hidden;
  }
  .card-front { top: 108px; background: var(--teal); }
  .card-back { top: 493px; background: var(--paper); }

  /* Front */
  .front-brand {
    position: absolute; left: 0; right: 0; top: 190px;
    display: flex; align-items: center; justify-content: center; gap: 12px;
    color: var(--white); font-weight: 500; font-size: 24px; letter-spacing: 3px;
    text-transform: uppercase;
  }
  .front-brand .brand-dot {
    width: 14px; height: 14px; border-radius: 50%; background: var(--white);
  }
  .front-url {
    position: absolute; left: 0; right: 0; top: 290px; text-align: center;
    color: var(--white); font-size: 14px; letter-spacing: 4.6px;
  }

  /* Back */
  .back-brand {
    position: absolute; left: 40px; width: 290px; top: 176px;
    display: flex; align-items: center; justify-content: center; gap: 10px;
    color: var(--teal); font-weight: 500; font-size: 18px; letter-spacing: 2px;
    text-transform: uppercase;
  }
  .back-brand .brand-dot {
    width: 12px; height: 12px; border-radius: 50%; background: var(--red);
  }
  .divider {
    position: absolute; left: 328px; top: 85px; width: 1px; height: 172px;
    background: #c9c9c9;
  }
  .contact { position: absolute; left: 351px; top: 82px; }
  .contact-name {
    font-family: "Roboto Condensed", Arial, sans-serif; font-weight: 700;
    font-size: 25px; color: var(--teal); line-height: 1; text-transform: uppercase;
  }
  .contact-title {
    font-family: "Roboto Condensed", Arial, sans-serif; font-weight: 500;
    font-size: 15px; color: var(--red); margin-top: 3px; text-transform: uppercase;
  }
  .contact-org { margin-top: 13px; font-size: 14px; font-weight: 700; color: var(--ink-strong); line-height: 18px; }
  .contact-address { font-size: 14px; color: var(--ink); line-height: 18px; }
  .contact-lines { list-style: none; margin-top: 10px; }
  .contact-lines li {
    display: flex; align-items: center; gap: 8px;
    font-size: 14px; color: var(--ink); line-height: 19px;
  }
  .contact-lines svg { width: 13px; height: 13px; flex: none; fill: var(--teal); }

  .band { position: absolute; left: 0; right: 0; bottom: 0; height: 14px; }
</style>
</head>
<body>
<main class="canvas">

  <section class="card card-front" aria-label="Card front">
    <div class="front-brand"><span class="brand-dot"></span>Harbor Home Alliance</div>
    <p class="front-url">www.harborhome.org</p>
  </section>

  <section class="card card-back" aria-label="Card back">
    <div class="back-brand"><span class="brand-dot"></span>Harbor Home Alliance</div>
    <div class="divider"></div>

    <div class="contact">
      <h1 class="contact-name">Daniel Reyes</h1>
      <p class="contact-title">CEO/Founder</p>
      <p class="contact-org">Harbor Home Alliance</p>
      <p class="contact-address">1420 Willow Crest Road<br>Juneau, Alaska 99801</p>
      <ul class="contact-lines">
        <li>
          <svg viewBox="0 0 16 16" aria-hidden="true"><path d="M3.6 1.2l2.3 2.6c.4.4.4 1 0 1.4L4.8 6.4c.9 2 2.5 3.6 4.6 4.6l1.2-1.1c.4-.4 1-.4 1.4 0l2.6 2.3c.4.4.4 1 0 1.4l-1.3 1.3C11.4 16 1 6.6.1 2.7L1.2 1.2c.7-.5 1.8-.5 2.4 0z"/></svg>
          555 018 2740
        </li>
        <li>
          <svg viewBox="0 0 16 16" aria-hidden="true"><path d="M1 3h14v1.2L8 8.6 1 4.2z"/><path d="M1 5.6l7 4.4 7-4.4V13H1z"/></svg>
          daniel@harborhome.org
        </li>
        <li>
          <svg viewBox="0 0 16 16" aria-hidden="true"><circle cx="8" cy="8" r="7"/><path d="M4 5.5c1.5 0 2 1 3 1s.5 2-.5 2.5S6 12 5 11.5 3 7 4 5.5zM9.5 3c1 .5 2 0 2.5 1s-1 1.5-1.5 2.5.5 2 1.5 2.5" fill="none" stroke="#f2f2f2" stroke-width="1"/></svg>
          www.harborhome.org
        </li>
      </ul>
    </div>

    <svg class="band" viewBox="0 0 600 14" preserveAspectRatio="none" aria-hidden="true">
      <polygon points="0,0 388,0 385,14 0,14" fill="var(--teal)"/>
      <polygon points="391,0 600,0 600,14 388,14" fill="var(--red)"/>
    </svg>
  </section>

</main>
</body>
</html>
```